Modern Attractive Letterhead for Veterinary House Call Business.

A letterhead which can be printed on A4, A5 and A6 paper sizes.
To have: ( our files to be uploaded)
1. Logo with Text
2. telephone
3. email
4. website
5. Address

Target Market(s)

60-85year mainly women pet owners. Also market include families, young professionals, busy people who have dogs and cats

Industry/Entity Type

Business

Requirements
Must have
• 1. Logo with Text ( provided)
• 2. telephone
• 3. email
• 4. website
• 5. Address
Nice to have
• Needs to be modern, preferably warm and caring in nature( if possible )
Should not have
• difficulty in printing A5 and A6

```html
<!DOCTYPE html>
<html lang="en">
<head>
<meta charset="utf-8">
<title>Fireside Pet Care Letterhead</title>
<link rel="stylesheet" href="https://fonts.googleapis.com/css2?family=Cinzel:wght@400;600&display=swap">
<style>
  :root {
    --paper-top: #ffffff;
    --paper-bottom: #ececef;
    --brand-blue: #2a68b4;
    --brand-green: #4e9a2c;
    --ink: #2b2b2b;
    --rule: #8a8a8a;
  }
  html, body {
    margin: 0;
    padding: 0;
    overflow: hidden;
    background: #f4f4f4;
  }
  .letterhead {
    position: relative;
    width: 948px;
    height: 1200px;
    overflow: hidden;
    background: linear-gradient(135deg, var(--paper-top) 0%, var(--paper-top) 35%, var(--paper-bottom) 100%);
    font-family: "Cinzel", serif;
    color: var(--ink);
  }
  .brand {
    position: absolute;
    left: 36px;
    top: 58px;
    display: flex;
    align-items: center;
    gap: 14px;
  }
  .brand-mark {
    width: 22px;
    height: 22px;
    border-radius: 50%;
    background: var(--brand-blue);
  }
  .brand-name {
    font-family: "Cinzel", serif;
    font-weight: 600;
    font-size: 40px;
    letter-spacing: 1px;
    color: var(--brand-blue);
    margin: 0;
    line-height: 1;
  }
  .postal-address {
    position: absolute;
    left: 670px;
    top: 62px;
    padding-left: 11px;
    border-left: 1px solid var(--rule);
    font-size: 17px;
    line-height: 24px;
    font-style: normal;
    letter-spacing: 0.5px;
  }
  .contact-list {
    position: absolute;
    left: 29px;
    top: 1120px;
    margin: 0;
    padding: 0;
    list-style: none;
    font-size: 14px;
    letter-spacing: 0.4px;
  }
  .contact-item {
    display: flex;
    align-items: center;
    gap: 7px;
    height: 21px;
  }
  .contact-icon {
    width: 12px;
    height: 12px;
    flex: none;
  }
</style>
</head>
<body>
  <main class="letterhead">
    <header>
      <div class="brand">
        <span class="brand-mark"></span>
        <h1 class="brand-name">Fireside Pet Care</h1>
      </div>
      <address class="postal-address">
        PO Box 4821 Kelvin Grove<br>
        QLD 4059
      </address>
    </header>

    <footer>
      <ul class="contact-list">
        <li class="contact-item">
          <svg class="contact-icon" viewBox="0 0 12 12" aria-hidden="true">
            <circle cx="6" cy="6" r="5.4" fill="none" stroke="var(--brand-green)" stroke-width="1"/>
            <path d="M4 3.2 L5 3 L5.6 4.6 L4.9 5.2 Q5.6 6.6 6.8 7.1 L7.4 6.4 L9 7 L8.8 8 Q6.5 8.8 4.4 6 Q3.5 4.4 4 3.2Z" fill="var(--brand-green)"/>
          </svg>
          <span>0491552308</span>
        </li>
        <li class="contact-item">
          <svg class="contact-icon" viewBox="0 0 12 12" aria-hidden="true">
            <rect x="0.6" y="2.4" width="10.8" height="7.4" rx="1" fill="var(--brand-green)"/>
            <path d="M1 3 L6 6.8 L11 3" fill="none" stroke="#ffffff" stroke-width="1"/>
          </svg>
          <span>HELLO@FIRESIDEPETCARE.COM.AU</span>
        </li>
        <li class="contact-item">
          <svg class="contact-icon" viewBox="0 0 12 12" aria-hidden="true">
            <circle cx="6" cy="6" r="5.3" fill="none" stroke="var(--brand-green)" stroke-width="1.1"/>
            <ellipse cx="6" cy="6" rx="2.3" ry="5.3" fill="none" stroke="var(--brand-green)" stroke-width="1"/>
            <path d="M0.8 6 H11.2 M1.6 3.4 H10.4 M1.6 8.6 H10.4" stroke="var(--brand-green)" stroke-width="0.9"/>
          </svg>
          <span>WWW.FIRESIDEPETCARE.COM.AU</span>
        </li>
      </ul>
    </footer>
  </main>
</body>
</html>
```